Flyer for the Radiant Harvest Worship Day

I am looking to create a flyer for a one day prayer retreat our church is organizing.
This flyer will be posted on social media, websites and will also be printed so it can be mailed to people.
I am looking for something professional, with good use of our logo and band colors (logo colors).
I am counting on the designer's skill, creativity, art and knowledge of media communication to produce a flyer that will effectively and quickly convey the message we are trying to spread.
CONTENT OF THE FLYER:
Event title: Radiant Harvest Worship Day
Date: Tuesday July 2nd, 2019
Time: 11:00AM - 7:00PM
Belmora Hotel, 4875 Wexley Avenue, Portland, Maine 04102 (Room: Juniper)
Event Key words to highlight what the event is about: Prayer, Sharing the Word, Panel discussion, prophecy, Impartation.
Key phrases:
A one day prayer retreat.
Jesus Chris is Lord
Contact info:
www.tolvex.org
Phone: 207 555 3184
Email: contact@brookhavenfold.org

```html
<!DOCTYPE html>
<html lang="en">
<head>
<meta charset="utf-8">
<title>Radiant Harvest Worship Day</title>
<link rel="stylesheet" href="https://fonts.googleapis.com/css2?family=Arimo:wght@400;700&display=swap">
<style>
  :root {
    --navy: #003a5c;
    --orange: #f7941d;
    --cream: #f4f1b4;
    --white: #ffffff;
    --frame: #6b6b6b;
    --bar-line: #c9d3db;
  }
  * { margin: 0; padding: 0; box-sizing: border-box; }
  html, body {
    width: 882px; height: 1200px; overflow: hidden;
    background: var(--white);
    font-family: "Arimo", Helvetica, Arial, sans-serif;
  }
  .flyer {
    position: absolute; left: 51px; top: 49px;
    width: 749px; height: 1059px;
    border: 1px solid var(--frame);
    background: var(--white);
    overflow: hidden;
  }
  .band-top {
    position: absolute; left: 0; top: 0; width: 100%; height: 25px;
    background: var(--orange);
  }
  .hero-image {
    position: absolute; left: 180px; top: 150px; width: 550px; height: 495px;
    background: radial-gradient(ellipse at 55% 45%, #8a7a6e 0%, #b9ada3 28%, #e6e1dc 55%, #ffffff 78%);
  }
  .title {
    position: absolute; left: 56px; top: 56px;
    color: var(--navy);
    font-weight: 700;
    font-size: 66px;
    line-height: 65px;
    letter-spacing: 0.5px;
    text-transform: uppercase;
  }
  .band-mid {
    position: absolute; left: 0; top: 651px; width: 100%; height: 18px;
    background: var(--orange);
  }
  .info-panel {
    position: absolute; left: 0; top: 669px; width: 100%; height: 390px;
    background: var(--navy);
    color: var(--white);
  }
  .tagline {
    position: absolute; top: 13px; width: 100%;
    text-align: center; font-size: 26px; line-height: 30px;
  }
  .motto {
    position: absolute; top: 52px; width: 100%;
    display: flex; justify-content: center; align-items: center; gap: 12px;
    color: var(--cream); font-size: 43px; line-height: 50px;
  }
  .motto::before, .motto::after {
    content: ""; width: 90px; height: 2px; background: var(--cream);
  }
  .brand {
    position: absolute; left: 66px; top: 175px;
    display: flex; align-items: center; gap: 10px;
  }
  .brand-dot {
    width: 26px; height: 26px; border-radius: 50%; background: var(--orange);
  }
  .brand-name {
    font-size: 40px; line-height: 44px; font-weight: 400; letter-spacing: 1px; color: var(--white);
  }
  .details {
    position: absolute; left: 299px; top: 155px;
    list-style: none; font-size: 17px; line-height: 28px;
  }
  .details li { display: flex; align-items: flex-start; gap: 9px; }
  .details svg { flex: none; margin-top: 5px; }
  .contact-bar {
    position: absolute; left: 47px; top: 309px; width: 654px; height: 50px;
    border: 1px solid var(--bar-line);
    display: flex; align-items: center; justify-content: center; gap: 16px;
    font-size: 20.5px;
  }
  .contact-bar span { display: flex; align-items: center; gap: 5px; white-space: nowrap; }
</style>
</head>
<body>
  <main class="flyer">
    <div class="band-top"></div>
    <div class="hero-image" role="img" aria-label="Aerial photo of a large crowd of people standing together in the shape of a cross"></div>
    <h1 class="title">Radiant<br>Harvest<br>Worship<br>Day</h1>
    <div class="band-mid"></div>

    <section class="info-panel">
      <p class="tagline">A one day prayer retreat.</p>
      <p class="motto">Jesus Chris is Lord</p>

      <div class="brand">
        <span class="brand-dot"></span>
        <span class="brand-name">TOLVEX</span>
      </div>

      <ul class="details">
        <li>
          <svg width="17" height="17" viewBox="0 0 17 17" fill="none" stroke="#fff" stroke-width="1.2"><rect x="1" y="2.5" width="15" height="13.5"/><line x1="1" y1="6" x2="16" y2="6"/><line x1="4.5" y1="0.5" x2="4.5" y2="4"/><line x1="12.5" y1="0.5" x2="12.5" y2="4"/><path d="M4 9h2M8 9h2M12 9h1M4 12h2M8 12h2M12 12h1"/></svg>
          <span>Date: Tuesday July 2nd, 2019</span>
        </li>
        <li>
          <svg width="17" height="17" viewBox="0 0 17 17" fill="none" stroke="#fff" stroke-width="1.2"><circle cx="8.5" cy="9" r="6.5"/><path d="M8.5 5.5V9l2.5 2"/><path d="M3 2.5l2-1.5M14 2.5l-2-1.5"/></svg>
          <span>Time: 11:00AM - 7:00PM</span>
        </li>
        <li>
          <svg width="17" height="17" viewBox="0 0 17 17" fill="none" stroke="#fff" stroke-width="1.2"><path d="M8.5 16s5-5.2 5-9a5 5 0 0 0-10 0c0 3.8 5 9 5 9z"/><circle cx="8.5" cy="7" r="1.8"/></svg>
          <span>Belmora Hotel, 4875 Wexley Avenue,<br>Portland, Maine 04102 (Room: Juniper)</span>
        </li>
      </ul>

      <div class="contact-bar">
        <span>
          <svg width="20" height="20" viewBox="0 0 20 20" fill="none" stroke="#fff" stroke-width="1.3"><circle cx="10" cy="10" r="8.5"/><ellipse cx="10" cy="10" rx="4" ry="8.5"/><path d="M1.5 10h17M3 5.5h14M3 14.5h14"/></svg>
          tolvex.org
        </span>
        <span>
          <svg width="26" height="20" viewBox="0 0 26 20" fill="none" stroke="#fff" stroke-width="1.3"><path d="M2 7c0-4 22-4 22 0l-1 2-4-1v-2c-3-1-9-1-12 0v2l-4 1z"/><path d="M7 10l-2 8h16l-2-8z"/><circle cx="13" cy="14" r="2"/></svg>
          207 555 3184
        </span>
        <span>
          <svg width="26" height="20" viewBox="0 0 26 20" fill="none" stroke="#fff" stroke-width="1.3"><rect x="1" y="3" width="20" height="14"/><path d="M1 3l10 8 10-8"/><circle cx="21" cy="15" r="3.5"/><path d="M19.6 15l1 1 2-2"/></svg>
          contact@brookhavenfold.org
        </span>
      </div>
    </section>
  </main>
</body>
</html>
```